Harborline Renewal Business Card Design

Professional and clean design. The design colors should flow with the logo. Two-sided card with the website on the back which is:

www.HarborlineRenewal.example.

"Specializing in Water Damage Restoration"

On the front I need the name, email, phone, and logo.

Name: Darnell Quisby
Email: Darnell@HarborlineRenewal.example
Phone: 555-318-2046 for now

I only have the Preview and Thumbnail right now but should have the source files uploaded within a day or two.

Target Market(s)

Flood victims, home owners with water damage from busted pipes etc...

Industry/Entity Type

Business

Contact Information for Business Card

Name: Darnell Quisby

Font styles to use
Serif
Sans Serif

Requirements
Must have
• Business Card Details Info

```html
<!DOCTYPE html>
<html lang="en">
<head>
<meta charset="utf-8">
<title>Harborline Renewal Business Card</title>
<link rel="stylesheet" href="https://fonts.googleapis.com/css2?family=Open+Sans:ital,wght@0,400;0,600;0,700;1,400;1,600&display=swap">
<style>
  :root {
    --backdrop: #8c8c8c;
    --sky: #00acd8;
    --ocean: #2693d4;
    --mist: #55c0ec;
    --brand: #2b8fd0;
    --white: #ffffff;
  }
  * { margin: 0; padding: 0; box-sizing: border-box; }
  html, body {
    width: 1200px; height: 900px; overflow: hidden;
    background: var(--backdrop);
    font-family: "Open Sans", Arial, sans-serif;
  }
  .canvas { position: relative; width: 1200px; height: 900px; }
  .card {
    position: absolute; left: 250px; width: 700px; height: 400px;
    overflow: hidden; box-shadow: 0 6px 18px rgba(0,0,0,0.25);
  }

  /* Back side */
  .card-back { top: 30px; background: var(--white); }
  .back-band-top { position: absolute; top: 0; left: 0; right: 0; height: 58px; background: var(--sky); }
  .back-band-bottom {
    position: absolute; left: 0; right: 0; bottom: 0; height: 150px; background: var(--sky);
    display: flex; justify-content: center; padding-top: 14px;
  }
  .back-website {
    position: absolute; top: 72px; width: 100%; text-align: center;
    color: var(--brand); font-size: 14px; font-style: italic; font-weight: 600;
  }
  .brand-mark {
    position: absolute; top: 100px; width: 100%;
    display: flex; flex-direction: column; align-items: center; gap: 10px;
  }
  .brand-dot { width: 62px; height: 62px; border-radius: 50%; background: var(--brand); }
  .brand-name { color: var(--brand); font-size: 36px; font-weight: 600; letter-spacing: 1px; }
  .tagline { color: var(--white); font-size: 18px; font-style: italic; font-weight: 600; }

  /* Front side */
  .card-front { top: 460px; background: var(--ocean); }
  .front-decor { position: absolute; left: 0; top: 0; }
  .contact-block {
    position: absolute; right: 40px; top: 0; height: 100%;
    text-align: right; color: var(--white);
  }
  .holder-name { position: absolute; right: 0; top: 110px; white-space: nowrap; font-size: 22px; font-weight: 700; }
  .contact-list { position: absolute; right: 0; top: 240px; list-style: none; white-space: nowrap; }
  .contact-list li {
    display: flex; justify-content: flex-end; align-items: center; gap: 8px;
    font-size: 17px; line-height: 27px;
  }
  .contact-list svg { width: 15px; height: 15px; }
</style>
</head>
<body>
<main class="canvas">

  <section class="card card-back" aria-label="Card back">
    <div class="back-band-top"></div>
    <p class="back-website">www.HarborlineRenewal.example</p>
    <div class="brand-mark">
      <span class="brand-dot"></span>
      <span class="brand-name">Harborline Renewal</span>
    </div>
    <div class="back-band-bottom">
      <p class="tagline">Specializing in Water Damage Restoration</p>
    </div>
  </section>

  <section class="card card-front" aria-label="Card front">
    <svg class="front-decor" width="700" height="400" viewBox="0 0 700 400">
      <path d="M0 0 H290 C345 90 360 250 240 400 H0 Z" fill="var(--mist)"/>
      <path d="M0 0 H260 C320 90 320 250 200 400 H0 Z" fill="var(--white)"/>
      <circle cx="90" cy="160" r="170" fill="var(--mist)" opacity="0.55"/>
    </svg>
    <div class="contact-block">
      <h1 class="holder-name">Darnell Quisby</h1>
      <ul class="contact-list">
        <li>555-318-2046
          <svg viewBox="0 0 16 16" aria-hidden="true"><path d="M3 2l3 0 1 3-2 1.5a9 9 0 0 0 4.5 4.5L11 9l3 1v3c0 1-1 1.5-2 1.5A11 11 0 0 1 1.5 4C1.5 3 2 2 3 2z" fill="var(--white)"/></svg>
        </li>
        <li>Darnell@HarborlineRenewal.example
          <svg viewBox="0 0 16 16" aria-hidden="true"><rect x="1" y="3" width="14" height="10" fill="var(--white)"/><path d="M1 3l7 6 7-6" fill="none" stroke="var(--ocean)" stroke-width="1.4"/></svg>
        </li>
        <li>www.HarborlineRenewal.example
          <svg viewBox="0 0 16 16" aria-hidden="true"><g fill="none" stroke="var(--white)" stroke-width="2" stroke-linecap="round"><path d="M7 9l2-2"/><path d="M6 7L4 9a2.5 2.5 0 0 0 3.5 3.5L9.5 10.5"/><path d="M10 9l2-2A2.5 2.5 0 0 0 8.5 3.5L6.5 5.5"/></g></svg>
        </li>
      </ul>
    </div>
  </section>

</main>
</body>
</html>
```